Real Estate Company
Residential & Commercial
Sales & Property Management

would like to use the logo i uploaded but would really love a black back ground...I think with the gold fleur dis lis and the maroon lettering it would really look great!

Industry/Entity Type

Business

Contact Information for Business Card

Bayou Hearth Realty Group
Danielle Forbis
Broker/Owner
337-284-6093 Cell
337-726-0348 Office
8142 Willet Rd Pelican Bend LA 70612

```html
<!DOCTYPE html>
<html lang="en">
<head>
<meta charset="utf-8">
<title>Bayou Hearth Realty Group – Business Card</title>
<link rel="stylesheet" href="https://fonts.googleapis.com/css2?family=Roboto+Condensed:ital,wght@0,300;0,400;0,700;1,300&display=swap">
<style>
  :root {
    --page: #ffffff;
    --card-edge: #231f20;
    --card-glow: #4a4a4b;
    --ink: #ffffff;
    --ink-soft: #f1f1f1;
    --accent-red: #c4262e;
    --accent-gold: #f2e64d;
  }
  * { margin: 0; padding: 0; box-sizing: border-box; }
  html, body {
    width: 1200px;
    height: 1047px;
    overflow: hidden;
    background: var(--page);
    font-family: "Roboto Condensed", "Arial Narrow", sans-serif;
  }
  .canvas {
    position: relative;
    width: 1200px;
    height: 1047px;
  }
  .card {
    position: absolute;
    width: 665px;
    height: 380px;
    background: radial-gradient(ellipse 60% 70% at 50% 50%, var(--card-glow) 0%, #3a3a3b 45%, var(--card-edge) 100%);
    color: var(--ink);
  }
  .card--front { left: 85px; top: 70px; }
  .card--back  { left: 385px; top: 485px; }

  /* Front */
  .brand {
    position: absolute;
    left: 140px;
    top: 95px;
    width: 360px;
    height: 130px;
    display: flex;
    align-items: center;
    gap: 18px;
  }
  .brand__mark {
    flex: none;
    width: 36px;
    height: 36px;
    border-radius: 50%;
    background: var(--accent-gold);
  }
  .brand__name {
    font-weight: 400;
    font-size: 40px;
    line-height: 1.1;
    color: var(--ink);
  }
  .brand__rule {
    position: absolute;
    left: 223px;
    top: 247px;
    width: 267px;
    height: 2px;
    background: var(--accent-red);
  }
  .website {
    position: absolute;
    left: 0;
    width: 100%;
    top: 260px;
    padding-left: 30px;
    text-align: center;
    font-weight: 400;
    font-size: 23px;
    color: var(--ink);
  }

  /* Back */
  .person {
    position: absolute;
    left: 33px;
    top: 38px;
  }
  .person__name {
    font-weight: 700;
    font-size: 26px;
    line-height: 1.2;
  }
  .person__title {
    font-weight: 300;
    font-style: italic;
    font-size: 24px;
    line-height: 1.3;
    color: var(--ink-soft);
  }
  .contact {
    position: absolute;
    right: 35px;
    bottom: 22px;
    text-align: right;
    font-style: normal;
    font-weight: 300;
    font-size: 26px;
    line-height: 39px;
    color: var(--ink);
  }
</style>
</head>
<body>
<main class="canvas">
  <section class="card card--front" aria-label="Card front">
    <div class="brand">
      <span class="brand__mark" aria-hidden="true"></span>
      <h1 class="brand__name">Bayou Hearth<br>Realty Group</h1>
    </div>
    <div class="brand__rule" aria-hidden="true"></div>
    <p class="website">www.danielleforbis.com</p>
  </section>

  <section class="card card--back" aria-label="Card back">
    <div class="person">
      <h2 class="person__name">Danielle Forbis,</h2>
      <p class="person__title">Broker/Owner</p>
    </div>
    <address class="contact">
      <div>337.284.6093 Cell</div>
      <div>337.726.0348 Office</div>
      <div>8142 Willet Rd., Pelican Bend LA 70612</div>
    </address>
  </section>
</main>
</body>
</html>
```